One of a kind service business!

We are the only ocean freight auditing company in the entire world that does what we do. We provide a innovative service in auditing our clients invoices for billing errors as it relates to the import and export of their products anywhere in the world. We'd like to retain the current logo - but we are open to any interesting concepts that can complete the card.

Target Market(s)

C-Level and Senior Financial executives

Industry/Entity Type

Auditing

Requirements
Must have

• ONE SIDED ONLY
Should not have
• no cartoonish images

```html
<!DOCTYPE html>
<html lang="en">
<head>
<meta charset="utf-8">
<title>Tidemark Audit – Business Card</title>
<link rel="stylesheet" href="https://fonts.googleapis.com/css2?family=Arimo:wght@400;700&display=swap">
<style>
  :root {
    --page-bg: #e6e7e8;
    --card-bg: #ffffff;
    --brand-blue: #0b78b1;
    --brand-green: #3db27e;
    --text-dark: #2b2b2b;
    --text-light: #ffffff;
  }
  * { box-sizing: border-box; margin: 0; padding: 0; }
  html, body {
    width: 1200px;
    height: 944px;
    overflow: hidden;
    background: var(--page-bg);
    font-family: "Arimo", Arial, sans-serif;
  }
  .card {
    position: absolute;
    left: 100px;
    top: 186px;
    width: 1000px;
    height: 572px;
    background: var(--card-bg);
    border-radius: 36px;
    overflow: hidden;
    box-shadow: 0 6px 18px rgba(0,0,0,0.18);
  }
  .card__waves {
    position: absolute;
    inset: 0;
    width: 1000px;
    height: 572px;
  }
  .wave--green { fill: var(--brand-green); }
  .wave--blue { fill: var(--brand-blue); }

  .brand {
    position: absolute;
    left: 52px;
    top: 82px;
    display: flex;
    align-items: center;
    gap: 16px;
    color: var(--brand-blue);
    font-weight: 700;
    font-size: 62px;
    line-height: 1;
    letter-spacing: 1px;
  }
  .brand__mark {
    width: 26px;
    height: 26px;
    background: var(--brand-blue);
  }

  .contact {
    position: absolute;
    left: 82px;
    color: var(--text-dark);
    font-size: 29px;
    line-height: 34px;
    list-style: none;
  }
  .contact--address { top: 214px; }
  .contact--lines { top: 330px; }
  .contact__item {
    display: flex;
    align-items: flex-start;
  }
  .contact__icon {
    width: 22px;
    height: 22px;
    margin: 6px 12px 0 0;
    flex: none;
    fill: var(--brand-green);
  }
  .contact__text--indent { padding-left: 34px; }

  .person {
    position: absolute;
    left: 640px;
    width: 320px;
    top: 452px;
    text-align: center;
    color: var(--text-light);
  }
  .person__name { font-size: 40px; line-height: 46px; }
  .person__role { font-size: 25px; line-height: 30px; }
</style>
</head>
<body>
  <div class="card">
    <svg class="card__waves" viewBox="0 0 1000 572" aria-hidden="true">
      <path class="wave--green" d="M612 0 C 680 90, 690 180, 610 300 C 540 400, 500 470, 493 572 L 1000 572 L 1000 0 Z"/>
      <path class="wave--blue" d="M724 0 C 760 110, 700 220, 620 300 C 585 340, 580 420, 583 572 L 1000 572 L 1000 0 Z"/>
    </svg>

    <div class="brand">
      <span>Tidemark Audit</span>
      <span class="brand__mark"></span>
    </div>

    <ul class="contact contact--address">
      <li class="contact__item">
        <svg class="contact__icon" viewBox="0 0 22 22"><path d="M11 2 L21 11 H18 V20 H13 V14 H9 V20 H4 V11 H1 Z"/></svg>
        <span>Riverside Business Park</span>
      </li>
      <li class="contact__text--indent">Harbour Lane 18, Prague</li>
      <li class="contact__text--indent">Czech Republic 10000</li>
    </ul>

    <ul class="contact contact--lines">
      <li class="contact__item">
        <svg class="contact__icon" viewBox="0 0 22 22"><path d="M11 1 A10 10 0 1 0 11.01 1 Z M8 5 L10 8 L8.5 10 C9.5 12 10.5 13 12 13.5 L14 12 L17 14 L15.5 17 C10 17 5 12 5 6.5 Z" fill-rule="evenodd"/></svg>
        <span>+420 200 555 010</span>
      </li>
      <li class="contact__item">
        <svg class="contact__icon" viewBox="0 0 22 22"><path d="M6 1 H16 V21 H6 Z M8 4 V14 H14 V4 Z" fill-rule="evenodd"/></svg>
        <span>+420 600 555 021</span>
      </li>
      <li class="contact__item">
        <svg class="contact__icon" viewBox="0 0 22 22"><path d="M11 1 A10 10 0 1 0 11.01 1 Z M8 5 L10 8 L8.5 10 C9.5 12 10.5 13 12 13.5 L14 12 L17 14 L15.5 17 C10 17 5 12 5 6.5 Z" fill-rule="evenodd"/></svg>
        <span>+1 555 010 4477 - USA</span>
      </li>
      <li class="contact__item">
        <svg class="contact__icon" viewBox="0 0 22 22"><path d="M6 2 H16 V8 H20 V18 H2 V8 H6 Z M8 4 V8 H14 V4 Z M6 11 V14 H16 V11 Z" fill-rule="evenodd"/></svg>
        <span>+420 200 555 090</span>
      </li>
      <li class="contact__item">
        <svg class="contact__icon" viewBox="0 0 22 22"><circle cx="11" cy="11" r="10"/></svg>
        <span>www.tidemarkaudit.net</span>
      </li>
      <li class="contact__item">
        <svg class="contact__icon" viewBox="0 0 22 22"><path d="M1 9 L11 2 L21 9 V20 H1 Z M3 10 L11 16 L19 10 V18 H3 Z" fill-rule="evenodd"/></svg>
        <span>danielm@tidemarkaudit.net</span>
      </li>
    </ul>

    <div class="person">
      <p class="person__name">Daniel Marsh</p>
      <p class="person__role">CEO</p>
    </div>
  </div>
</body>
</html>
```